complete redesign of VitalPlate.com

VITALPLATE.COM
MAIN MANU

We need it cut into HTML / Wordpress Friendly.... Our developer will handle all the WP / PHP coding, but we need it placed into HTML format so he can put into wordpress.

Please see the old vitalplate.com by visiting www.vitalplate.com... we want something completely different, but... just use this site for reference as to audience, theme, etc... we want something where it is science meets diet in helping fight cancer :)

WE NEED SOMETHING MORE MODERN AND MEDICAL IN TERMS OF DESIGN

See below:

1 CANCER NEWS
2 NUTRITION DIAGNOSTICS
3 DIET STEPS
4 DIET SUPPLEMENTS IN CANCER 
5 DICTIONARY OF MARKINGS ON FOOD
6 MERIBLEND VIDEOS
7 YOUR INDIVIDUAL DIET - SUBSCRIPTION

a. CANCER NEWS - latest articles relating to cancer prevention research treatments

b. NUTRITION DIAGNOSTICS -  description of the research that must be done to determine the degree of malnutrition of the body a place on the charts
pictures, etc.

c. DIET STEPS 
(sub menu - @)
¥ prevention of oncological - @
¥ diet chemotherapy - @
¥ diet in radiotherapy - @
¥ hormonal diet - @
¥ diet during convalescence - @

d. DIET SUPPLEMENTS IN CANCER - articles describing various supplements summary tables, etc.

e. DICTIONARY OF MARKINGS ON FOOD - composition, translation of labels on food, itd.

f. MERIBLEND VIDEOS 
(sub menu - @)
¥ healthy cooking - @
¥ meal preparation - @
¥ storage of food - @
¥ eco food - @
¥ rehabilitation - @
¥ yoga - @
¥ exercises - @
¥ psycho-oncology training - @
¥ music therapy - @

g. YOUR INDIVIDUAL DIET -  individual personalized diet for subscribing. We
add this point by developing a system of diet.

After 3 months, we will add special individual programs that mix diet, exercise and psychological lectures

Industry/Entity Type

Medical

Logo Text

Vital Plate / VitalPlate.com

Number of Pages Required

5+ page

Font styles to use
Sans Serif

Colors
ec1f27
9bcb3c
ffffff

Requirements
Must have
• HTML/CSS

```html
<!DOCTYPE html>
<html lang="en">
<head>
<meta charset="utf-8">
<title>Vital Plate — You are what you eat</title>
<link href="https://fonts.googleapis.com/css2?family=Open+Sans:ital,wght@0,300;0,400;0,600;0,700;0,800;1,400&display=swap" rel="stylesheet">
<style>
:root{
  --blue:#2d7dcb;
  --blue-title:#1f6fc0;
  --blue-dark:#1d5ea6;
  --blue-deep:#1a4f8f;
  --red:#e3222a;
  --text:#333;
  --muted:#555;
  --grey-band:#e6e6e6;
  --white:#fff;
}
*{margin:0;padding:0;box-sizing:border-box}
html,body{width:1200px;height:2848px;overflow:hidden}
body{font-family:"Open Sans",Arial,sans-serif;color:var(--text);background:var(--white);position:relative}
section,header,footer,nav{position:absolute;left:0;width:1200px}
.abs{position:absolute}

/* header */
.site-header{top:0;height:85px;background:var(--white)}
.brand{left:99px;top:18px;display:flex;align-items:center;gap:12px}
.brand-dot{width:50px;height:50px;border-radius:50%;background:var(--blue)}
.brand-name{font-size:38px;font-weight:700;color:var(--red);letter-spacing:-.5px}
.phone{left:722px;top:22px;display:flex;align-items:center;gap:12px;font-size:15px;color:var(--muted)}
.phone-icon{width:42px;height:42px;border-radius:50%;background:var(--blue);display:flex;align-items:center;justify-content:center}
.phone b{color:var(--red);font-weight:700}
.login{left:967px;top:24px;width:134px;height:38px;background:var(--red);color:var(--white);font-size:12px;font-weight:700;display:flex;align-items:center;justify-content:center;border-radius:2px}

/* nav */
.main-nav{top:85px;height:54px;background:linear-gradient(#3c8ddb,#2a75c2)}
.main-nav ul{list-style:none;display:flex;position:absolute;left:101px;top:0;height:54px}
.main-nav li{color:var(--white);font-size:11.5px;font-weight:700;line-height:15px;padding:11px 22px 0 22px;text-transform:uppercase}
.main-nav li.active{background:var(--red)}

/* hero */
.hero{top:139px;height:488px;background:linear-gradient(90deg,#f4f4f4,#ececec 55%,#e4e4e4)}
.hero-photo{left:560px;top:0;width:640px;height:488px;background:radial-gradient(ellipse at 60% 45%,#e6d4c8,#d8d8d8 55%,#ebebeb)}
.hero-title{left:101px;top:112px;font-size:50px;font-weight:700;color:var(--blue-title);line-height:58px}
.hero-sub{left:101px;top:166px;font-size:47px;font-weight:300;color:var(--red);line-height:56px}
.hero-text{left:101px;top:235px;width:520px;font-size:14px;line-height:25px;color:#444}
.hero-btn{left:101px;top:301px;width:167px;height:46px;background:var(--red);color:var(--white);font-size:12.5px;font-weight:700;display:flex;align-items:center;justify-content:center;border-radius:2px}
.dots{display:flex;gap:6px}
.dots span{width:8px;height:8px;border-radius:50%;background:#bbb}
.dots span.on{background:var(--blue)}
.hero .dots{left:103px;top:368px}

/* news */
.news{top:627px;height:287px;background:var(--blue)}
.section-title{left:0;width:1200px;text-align:center;font-size:24px;font-weight:700;color:var(--blue-title);text-transform:uppercase}
.news .section-title{top:40px;color:var(--white);display:flex;justify-content:center;align-items:center;gap:18px}
.news .section-title i{display:block;width:155px;height:1px;background:rgba(255,255,255,.8)}
.news-img{width:164px;height:126px;top:103px}
.news-img.a{left:99px;background:linear-gradient(135deg,#f3b24a,#e58a2a 50%,#f7e0b0)}
.news-img.b{left:621px;background:linear-gradient(135deg,#7fb8e6,#dbe9f5 55%,#eef4fb)}
.news-body{top:96px;width:280px;color:var(--white)}
.news-body h3{font-size:12.5px;font-weight:700;line-height:22px;text-transform:uppercase}
.news-body .date{font-size:11.5px;margin:2px 0 8px}
.news-body p{font-size:11.5px;line-height:21px}
.news .dots{left:580px;top:257px}
.news .dots span{width:6px;height:6px;background:rgba(255,255,255,.5)}
.news .dots span.on{background:var(--white)}

/* steps */
.steps{top:914px;height:341px}
.steps .section-title{top:52px}
.lead{left:0;width:1200px;text-align:center;font-size:12.5px;color:var(--muted)}
.steps .lead{top:90px}
.step{top:150px;width:200px;text-align:center}
.step-icon{width:104px;height:104px;border-radius:50%;background:var(--blue);margin:0 auto;display:flex;align-items:center;justify-content:center}
.step-num{margin-top:18px;font-size:13px;font-weight:700;color:var(--red)}
.step-name{font-size:13px;color:var(--text);margin-top:3px}
.chev{top:188px;font-size:30px;font-weight:700;color:#c9c9c9;letter-spacing:-6px}

/* diagnostics */
.diag{top:1255px;height:308px}
.diag-img{left:99px;top:20px;width:359px;height:241px;background:linear-gradient(135deg,#0c3f88,#2b86e0 55%,#6ab8f5)}
.diag-title{left:520px;top:37px;font-size:23px;font-weight:700;color:var(--blue-title)}
.diag-lead{left:524px;top:75px;width:560px;font-size:14px;line-height:25px;color:#444}
.diag-text{left:520px;top:134px;width:570px;font-size:11px;line-height:22px;color:#444}

/* supplements */
.supp{top:1563px;height:422px;background:var(--grey-band)}
.supp .section-title{top:57px}
.supp .lead{top:95px}
.card{top:152px;width:226px}
.card .ph{height:152px}
.card h4{margin-top:17px;font-size:12px;font-weight:700;line-height:21px;color:#333;text-transform:uppercase}
.ph.s1{background:linear-gradient(135deg,#e9f1df,#b8d78a 60%,#e4a640)}
.ph.s2{background:linear-gradient(135deg,#7a0d14,#c7222d 50%,#e2404a)}
.ph.s3{background:linear-gradient(180deg,#c0390f,#f08c1c 55%,#6a2a08)}
.ph.s4{background:radial-gradient(circle at 60% 50%,#8fd0ea,#1d5a86 55%,#0b2438)}

/* videos */
.videos{top:1985px;height:477px}
.videos .section-title{top:52px}
.videos .lead{top:90px}
.video{top:144px;width:313px;text-align:center}
.video .ph{height:209px;position:relative;display:flex;align-items:center;justify-content:center}
.video h4{margin-top:18px;font-size:13px;font-weight:700;color:#333;text-transform:uppercase}
.ph.v1{background:linear-gradient(135deg,#7a3b1c,#b5642c 45%,#5d8a2d)}
.ph.v2{background:radial-gradient(circle at 40% 60%,#2c5fa8,#b01c25 50%,#7a0c12)}
.ph.v3{background:linear-gradient(135deg,#f2f2f2,#e2d6cc 55%,#c9dbe9)}
.play{width:64px;height:64px;border-radius:50%;background:rgba(255,255,255,.85);display:flex;align-items:center;justify-content:center}
.videos .dots{left:589px;top:420px}
.videos .dots span{background:#ccc}
.videos .dots span.on{background:var(--red)}

/* subscribe */
.subscribe{top:2462px;height:78px;background:var(--blue)}
.subscribe-text{left:101px;top:27px;color:var(--white);font-size:12.5px;letter-spacing:-.2px;white-space:nowrap;line-height:24px}
.subscribe-text b{font-size:17px;font-weight:700;margin-right:3px;letter-spacing:0}
.email{left:627px;top:22px;width:474px;height:36px;background:var(--white);border-radius:18px;font-size:13px;color:#555;padding:9px 20px}
.sub-btn{left:982px;top:26px;width:115px;height:28px;background:var(--red);border-radius:14px;color:var(--white);font-size:11px;font-weight:700;display:flex;align-items:center;justify-content:center}

/* footer */
.site-footer{top:2540px;height:256px;background:var(--blue-dark);color:var(--white)}
.fcol{top:30px}
.fcol h5{font-size:13.5px;font-weight:700;margin-bottom:14px;text-transform:uppercase}
.fcol li{list-style:none;font-size:11.5px;line-height:21px}
.fnews p{font-size:12px;font-weight:600}
.fnews em{display:block;font-size:11px;margin-bottom:16px}
.contact p{font-size:11.5px;line-height:21px}
.social{display:flex;gap:10px;margin-top:16px}
.social span{width:28px;height:28px;border-radius:50%;background:var(--white)}
.bottom-bar{top:2796px;height:52px;background:var(--blue-deep);color:var(--white);font-size:11.5px}
.bottom-bar .row{left:0;width:1200px;top:17px;display:flex;justify-content:center;gap:36px;padding-left:40px}
</style>
</head>
<body>

<header class="site-header">
  <div class="abs brand"><span class="brand-dot"></span><span class="brand-name">Vitalplate</span></div>
  <div class="abs phone">
    <span class="phone-icon"><svg width="20" height="20" viewBox="0 0 24 24"><path fill="#fff" d="M6.6 10.8a15 15 0 0 0 6.6 6.6l2.2-2.2c.3-.3.7-.4 1-.2 1.1.4 2.3.6 3.6.6.6 0 1 .4 1 1V20c0 .6-.4 1-1 1A17 17 0 0 1 3 4c0-.6.4-1 1-1h3.5c.6 0 1 .4 1 1 0 1.3.2 2.5.6 3.6.1.3 0 .7-.2 1z"/></svg></span>
    <span>Phone : <b>( 5550 ) 214 870</b></span>
  </div>
  <div class="abs login">MEMBERS LOGIN</div>
</header>

<nav class="main-nav">
  <ul>
    <li class="active">Cancer<br>News</li>
    <li>Nutrition<br>Diagnostics</li>
    <li>Diet<br>Steps</li>
    <li>Diet Supplements<br>in Cancer</li>
    <li>Dictionary of<br>Markings on Food</li>
    <li>Meriblend<br>Videos</li>
    <li>Your Individual Diet<br>- Subscription</li>
  </ul>
</nav>

<section class="hero">
  <div class="abs hero-photo" role="img" aria-label="Woman eating a fresh vegetable salad from a bowl"></div>
  <div class="abs hero-title">Vitalplate</div>
  <div class="abs hero-sub">You are what you eat</div>
  <p class="abs hero-text">At VitalPlate.com we are &nbsp;diving into the science and chemistry of what we eat and how it effects our bodies in ways we could not imagine until recently.</p>
  <div class="abs hero-btn">READ MORE INFO</div>
  <div class="abs dots"><span class="on"></span><span></span><span></span><span></span></div>
</section>

<section class="news">
  <h2 class="abs section-title"><i></i>Cancer News<i></i></h2>
  <div class="abs news-img a" role="img" aria-label="Breakfast table with juice, pastries and bread"></div>
  <div class="abs news-body" style="left:286px">
    <h3>Lorem Ipsum is simply dummy text<br>of the printing</h3>
    <div class="date">Posted on 27 march 2015</div>
    <p>Lorem Ipsum is simply dummy text of the printing and typesetting industry. Lorem the industry's standard</p>
  </div>
  <div class="abs news-img b" role="img" aria-label="Smiling woman stretching in the morning"></div>
  <div class="abs news-body" style="left:808px">
    <h3>Lorem Ipsum is simply dummy text<br>of the printing</h3>
    <div class="date">Posted on 27 march 2015</div>
    <p>Lorem Ipsum is simply dummy text of the printing and typesetting industry. Lorem the industry's standard</p>
  </div>
  <div class="abs dots"><span class="on"></span><span></span><span></span><span></span></div>
</section>

<section class="steps">
  <h2 class="abs section-title">Diet Steps</h2>
  <p class="abs lead">Lorem Ipsum is simply dummy text of the printing and typesetting industry. Lorem Ipsum has been the industry's standard...</p>

  <div class="abs step" style="left:105px">
    <div class="step-icon"><svg width="52" height="52" viewBox="0 0 52 52" fill="none" stroke="#fff" stroke-width="4"><circle cx="22" cy="22" r="14"/><path d="M32 32l14 14" stroke-linecap="round"/></svg></div>
    <div class="step-num">STEP 01</div><div class="step-name">Prevention of oncological</div>
  </div>
  <div class="abs chev" style="left:290px">&rsaquo;&rsaquo;</div>
  <div class="abs step" style="left:303px">
    <div class="step-icon"><svg width="40" height="56" viewBox="0 0 40 56" fill="none" stroke="#fff" stroke-width="3.5"><rect x="6" y="6" width="28" height="34" rx="4"/><path d="M12 18h16M12 26h16M20 40v12"/></svg></div>
    <div class="step-num">STEP 02</div><div class="step-name">Diet chemotherapy</div>
  </div>
  <div class="abs chev" style="left:488px">&rsaquo;&rsaquo;</div>
  <div class="abs step" style="left:500px">
    <div class="step-icon"><svg width="52" height="52" viewBox="0 0 52 52" fill="#fff"><rect x="8" y="8" width="12" height="38"/><rect x="8" y="8" width="36" height="12"/><rect x="26" y="24" width="8" height="14"/></svg></div>
    <div class="step-num">STEP 03</div><div class="step-name">Diet in radiotherapy</div>
  </div>
  <div class="abs chev" style="left:686px">&rsaquo;&rsaquo;</div>
  <div class="abs step" style="left:698px">
    <div class="step-icon"><svg width="58" height="52" viewBox="0 0 58 52" fill="none" stroke="#fff" stroke-width="4"><circle cx="20" cy="30" r="11"/><path d="M20 41v9M14 46h12"/><circle cx="36" cy="24" r="11"/><path d="M44 16l8-8M44 8h8v8"/></svg></div>
    <div class="step-num">STEP 04</div><div class="step-name">Hormonal diet</div>
  </div>
  <div class="abs chev" style="left:884px">&rsaquo;&rsaquo;</div>
  <div class="abs step" style="left:894px">
    <div class="step-icon"><svg width="50" height="54" viewBox="0 0 50 54" fill="none" stroke="#fff" stroke-width="3.5"><rect x="5" y="5" width="40" height="44" rx="6"/><circle cx="25" cy="21" r="8"/><path d="M25 21l4-4M15 34h6M29 34h6"/></svg></div>
    <div class="step-num">STEP 05</div><div class="step-name">Diet during convalescence</div>
  </div>
</section>

<section class="diag">
  <div class="abs diag-img" role="img" aria-label="Glowing anatomical figure running beside a heartbeat line"></div>
  <h2 class="abs diag-title">NUTRITION DIAGNOSTICS</h2>
  <p class="abs diag-lead">Lorem Ipsum is simply dummy text of the printing and typesetting industry has been the industry's standard dummy</p>
  <p class="abs diag-text">At VitalPlate.com we are &nbsp;diving into the science and chemistry of what we eat and how it effects our bodies in ways we could not imagine until recently. It is true - you are what you eat, and we intend to show you how you can eat your way to a healthy and &nbsp;cancer free life. At VitalPlate.com we are &nbsp;diving into the science and chemistry of what we eat and how it effects our bodies in ways we could not imagine until recently. It is true - to show you how you can eat your way to a healthy and &nbsp;cancer free life.</p>
</section>

<section class="supp">
  <h2 class="abs section-title">Diet Supplements in Cancer</h2>
  <p class="abs lead">Lorem Ipsum is simply dummy text of the printing and typesetting industry. Lorem Ipsum has been the industry's standard...</p>
  <div class="abs card" style="left:99px"><div class="ph s1" role="img" aria-label="Woman with fresh fruit and vegetables"></div><h4>Lorem Ipsum is simply dummy<br>text of the printing</h4></div>
  <div class="abs card" style="left:357px"><div class="ph s2" role="img" aria-label="Red blood cells close up"></div><h4>Lorem Ipsum is simply dummy<br>text of the printing</h4></div>
  <div class="abs card" style="left:615px"><div class="ph s3" role="img" aria-label="Person in a wheat field at sunset"></div><h4>Lorem Ipsum is simply dummy<br>text of the printing</h4></div>
  <div class="abs card" style="left:874px"><div class="ph s4" role="img" aria-label="Digital profile with a glowing molecular sphere"></div><h4>Lorem Ipsum is simply dummy<br>text of the printing</h4></div>
</section>

<section class="videos">
  <h2 class="abs section-title">Meriblend Videos</h2>
  <p class="abs lead">Lorem Ipsum is simply dummy text of the printing and typesetting industry. Lorem Ipsum has been the industry's standard...</p>
  <div class="abs video" style="left:99px"><div class="ph v1" role="img" aria-label="Vegetables and bread on a wooden table"><span class="play"><svg width="22" height="24" viewBox="0 0 22 24"><path d="M3 2l17 10L3 22z" fill="#2d7dcb"/></svg></span></div><h4>Healthy Cooking</h4></div>
  <div class="abs video" style="left:444px"><div class="ph v2" role="img" aria-label="Blood cells and virus particles"><span class="play"><svg width="22" height="24" viewBox="0 0 22 24"><path d="M3 2l17 10L3 22z" fill="#2d7dcb"/></svg></span></div><h4>Meal Preparation</h4></div>
  <div class="abs video" style="left:788px"><div class="ph v3" role="img" aria-label="Woman with a salad bowl and flying vegetables"><span class="play"><svg width="22" height="24" viewBox="0 0 22 24"><path d="M3 2l17 10L3 22z" fill="#2d7dcb"/></svg></span></div><h4>Storage of Food</h4></div>
  <div class="abs dots"><span class="on"></span><span></span></div>
</section>

<section class="subscribe">
  <div class="abs subscribe-text"><b>YOUR INDIVIDUAL DIET.</b> Individual personalized diet for subscribing</div>
  <div class="abs email">Enter your email id</div>
  <div class="abs sub-btn">SUBSCRIBE</div>
</section>

<footer class="site-footer">
  <div class="abs fcol" style="left:101px"><h5>Welcome</h5><ul>
    <li>Cancer News</li><li>Nutrition Diagnostics</li><li>Diet Steps</li><li>Diet Supplements In Cancer</li><li>Dictionary Of Markings On Food</li><li>Meriblend Videos</li><li>Your Individual Diet - Subscription</li></ul></div>
  <div class="abs fcol" style="left:363px"><h5>Videos</h5><ul>
    <li>Healthy cooking</li><li>Meal preparation</li><li>Storage of food</li><li>Eeco food</li><li>Rehabilitation</li><li>Yoga</li><li>Exercises</li><li>Psycho-oncology training</li></ul></div>
  <div class="abs fcol fnews" style="left:581px"><h5>Latest News</h5>
    <p>Lorem Ipsum is simply dummy text</p><em>Posted on 27 March 2015</em>
    <p>Lorem Ipsum is simply dummy text</p><em>Posted on 27 March 2015</em>
    <p>Lorem Ipsum is simply dummy text</p><em>Posted on 27 March 2015</em></div>
  <div class="abs fcol contact" style="left:889px"><h5>Contact Info</h5>
    <p>48 Harbor Lane, Westfield.</p><p>Region code : 480213</p>
    <p style="margin-top:10px;padding-left:24px">Phone : ( 5550 ) 214 870</p>
    <p style="padding-left:24px">Email : info@vitalplate.com</p>
    <div class="social"><span></span><span></span><span></span><span></span><span></span></div></div>
</footer>

<div class="abs bottom-bar" style="left:0;width:1200px">
  <div class="abs row"><span>© 2015. Vital Plate. All rights reserved.</span><span>Terms of Use</span><span>Privacy Policy</span><span>Site Map</span></div>
</div>

</body>
</html>
```